Stylish Business Cards Wanted

- DOUBLE SIDED Design Required -

High end, edgy cards for a corporate and personal stylist. Must include logo,
Name: Belinda Harwick
Title: Director and Stylist
telephone : +61 8 7142 5809
email: belinda@theloombriefing.example
website: theloombriefing.example
Tag: Corporate Workwear & Uniform Specialist | Personal Stylist
Would like nice icons for telephone, email, website

Target Market(s)

Businesses wanting stylish uniforms, people wanting stylish wardrobes

Industry/Entity Type

Corporate Workwear Stylist

Contact Information for Business Card

I would like black, white and gold foiling incorporated in the design - possibly a touch of the other colours on my branding guide attached Name: Belinda Harwick Title: Director and Stylist telephone : +61 8 7142 5809 email: belinda@theloombriefing.example website: theloombriefing.example Tag: Corporate Workwear & Uniform Specialist | Personal Stylist Would like nice icons for telephone, email, website

Font styles to use
Other font styles liked:
• Raleway

Colors

Designer to choose colors to be used in the design.

Requirements
Must have
• Gold foil accents

```html
<!DOCTYPE html>
<html lang="en">
<head>
<meta charset="utf-8">
<title>The Loom Briefing — Business Cards</title>
<link rel="stylesheet" href="https://fonts.googleapis.com/css2?family=Montserrat:wght@400;500&family=Raleway:wght@400;600&display=swap">
<style>
  :root {
    --backdrop: #262626;
    --card: #121212;
    --card-edge: #1c1c1c;
    --white: #f1f1f1;
    --grey: #b9b9b9;
    --gold: #d8b64a;
    --blind: #1a1a1a;
  }
  * { box-sizing: border-box; margin: 0; padding: 0; }
  html, body {
    width: 1200px; height: 868px; overflow: hidden;
    background: var(--backdrop);
  }
  .canvas {
    position: relative; width: 1200px; height: 868px;
    display: flex; align-items: center; justify-content: center; gap: 60px;
  }
  .card {
    position: relative; width: 500px; height: 286px;
    background: var(--card);
    border: 1px solid var(--card-edge);
    box-shadow: 0 18px 40px rgba(0,0,0,.45);
  }

  /* Front */
  .card-front { display: flex; flex-direction: column; align-items: center; justify-content: center; }
  .brand-name {
    font-family: "Raleway", sans-serif; font-weight: 600;
    font-size: 40px; letter-spacing: 1px; color: var(--white);
    margin-top: 10px;
  }
  .brand-mark {
    width: 12px; height: 12px; background: var(--gold);
    margin-bottom: 14px;
  }
  .tagline {
    position: absolute; bottom: 30px; left: 0; right: 0; text-align: center;
    font-family: "Montserrat", sans-serif; font-size: 9.5px; letter-spacing: 1.6px;
    color: var(--grey); text-transform: uppercase;
  }
  .tagline .divider { color: var(--gold); padding: 0 4px; }

  /* Back */
  .blind-brand {
    position: absolute; left: 34px; top: 50%; transform: translateY(-50%);
    font-family: "Raleway", sans-serif; font-weight: 600; font-size: 34px;
    color: var(--blind);
    text-shadow: 0 1px 0 #242424;
    line-height: 1.1;
  }
  .contact {
    position: absolute; right: 30px; top: 50%; transform: translateY(-50%);
    text-align: right; font-family: "Montserrat", sans-serif;
  }
  .contact-name {
    font-size: 17px; font-weight: 500; letter-spacing: 1px;
    color: var(--white); text-transform: uppercase;
  }
  .contact-title { font-size: 11px; color: var(--gold); margin: 3px 0 14px; }
  .contact-line {
    display: flex; align-items: center; justify-content: flex-end; gap: 8px;
    font-size: 10.5px; color: var(--grey); margin-top: 5px;
  }
  .contact-line svg { width: 12px; height: 12px; flex: none; }
</style>
</head>
<body>
<main class="canvas">

  <section class="card card-front" aria-label="Card front">
    <div class="brand-mark"></div>
    <div class="brand-name">The Loom Briefing</div>
    <p class="tagline">Corporate Workwear<span class="divider">|</span>Uniform Specialist<span class="divider">|</span>Personal Stylist</p>
  </section>

  <section class="card card-back" aria-label="Card back">
    <div class="blind-brand">The Loom<br>Briefing</div>
    <div class="contact">
      <p class="contact-name">Belinda Harwick</p>
      <p class="contact-title">Director &amp; Stylist</p>
      <p class="contact-line">+61 8 7142 5809
        <svg viewBox="0 0 12 12" aria-hidden="true"><path fill="var(--gold)" d="M3 1.2 4.6 3.6 3.7 4.6a6 6 0 0 0 3.7 3.7l1-.9 2.4 1.6-.8 1.6C6 10.6 1.4 6 1.4 2z"/></svg>
      </p>
      <p class="contact-line">belinda@theloombriefing.example
        <svg viewBox="0 0 12 12" aria-hidden="true"><rect x="1" y="2.5" width="10" height="7" fill="var(--gold)"/><path d="M1 2.5 6 6.6 11 2.5" fill="none" stroke="var(--card)" stroke-width="1"/></svg>
      </p>
      <p class="contact-line">theloombriefing.example
        <svg viewBox="0 0 12 12" aria-hidden="true"><circle cx="6" cy="6" r="5.2" fill="var(--gold)"/><g fill="none" stroke="var(--card)" stroke-width=".8"><ellipse cx="6" cy="6" rx="2.2" ry="5.2"/><path d="M.8 6h10.4"/></g></svg>
      </p>
    </div>
  </section>

</main>
</body>
</html>
```